Natural Medicine & Health/Fitness Coaching studio requires web page

Require a innovative web page for a studio that coaches clients to better health, nutrition and fitness. The studio compromises of Clinical Nutritionists, Naturopaths, Rehab Trainers, Personal Trainers and Sport Coaches. Would like to see earthy but bold designs emphasizing nutritional health and athletic performance.
Updates

Design only launched today.

Target Market(s)

All genders from 20's to 60's, as well as families

Industry/Entity Type

Nutritionist

Coding

Coded - Design and coding required

Number of Pages Required

3 page

Colors
abd037
3277b5
fbee3d
fece3e
33b8a4
f04a50

Requirements
Must have
• Online booking system, ability to message
• Home page
• Coaching/Fitness page
• Nutritional Medicine page
• Must be suitable for both Fitness and Nutrition

```html
<!DOCTYPE html>
<html lang="en">
<head>
<meta charset="utf-8">
<title>Verdant Form — Nutritional Therapy</title>
<link rel="stylesheet" href="https://fonts.googleapis.com/css2?family=Montserrat:wght@400;500;600;700;800&family=Open+Sans:wght@400;600&family=Dancing+Script:wght@600&display=swap">
<style>
:root{
  --green:#abd037;
  --green-deep:#7fae2a;
  --blue:#3277b5;
  --yellow:#fbee3d;
  --gold:#fece3e;
  --teal:#33b8a4;
  --red:#f04a50;
  --ink:#222;
  --muted:#6b6b6b;
  --white:#fff;
  --black:#0d0d0d;
}
*{box-sizing:border-box;margin:0;padding:0}
html,body{width:1200px;height:3172px;overflow:hidden}
body{font-family:"Open Sans",Arial,sans-serif;color:var(--ink);background:var(--white);position:relative}

/* header & hero */
.hero{position:absolute;left:0;top:0;width:1200px;height:660px;overflow:hidden}
.hero-photo{position:absolute;inset:0;background:linear-gradient(100deg,#f3f1ee 0%,#ece8e2 40%,#d9cfc4 62%,#c9b8a6 78%,#e9e3da 100%)}
.hero-produce{position:absolute;left:0;bottom:0;width:1200px;height:150px;background:linear-gradient(90deg,#5f8f2a 0%,#8cbf3a 18%,#e0a628 30%,#d33b2c 40%,#6a9d2e 55%,#b9d66a 70%,#4f7f24 100%);opacity:.85}
.site-nav{position:absolute;top:0;left:0;width:1200px;height:110px;display:flex;align-items:center;padding:0 120px}
.brand{display:flex;align-items:center;gap:10px;font-family:"Montserrat",sans-serif;font-weight:800;font-size:34px;color:var(--green-deep)}
.brand-dot{width:16px;height:16px;border-radius:50%;background:var(--green)}
.brand-sub{position:absolute;left:150px;top:74px;font-size:12px;color:var(--muted);letter-spacing:1px}
.nav-links{margin-left:auto;display:flex;gap:34px;list-style:none;font-family:"Montserrat",sans-serif;font-size:15px;font-weight:600;color:var(--white)}
.hero-copy{position:absolute;left:112px;top:210px}
.hero-title{font-family:"Montserrat",sans-serif;font-size:54px;line-height:1.05;color:var(--teal);font-weight:700}
.hero-title b{font-weight:800}
.hero-title .amp{color:var(--red)}
.hero-title .light{font-weight:500}
.hero-script{font-family:"Dancing Script",cursive;font-size:46px;line-height:1.15;color:var(--ink);margin-top:14px}
.btn{display:inline-block;font-family:"Montserrat",sans-serif;font-weight:700;font-size:14px;letter-spacing:1px;color:var(--white);border-radius:30px;padding:14px 32px}
.btn-blue{background:var(--blue)}
.btn-teal{background:var(--teal)}
.hero .btn{position:absolute;left:112px;top:456px}

/* about */
.eyebrow{font-family:"Montserrat",sans-serif;font-size:14px;letter-spacing:3px;font-weight:600}
.about .eyebrow{position:absolute;left:112px;top:724px;color:var(--teal)}
.about h2{position:absolute;left:112px;top:746px;font-family:"Montserrat",sans-serif;font-weight:500;font-size:58px;color:var(--blue)}
.about-rule{position:absolute;left:112px;top:822px;width:80px;height:3px;background:var(--teal)}
.about p{position:absolute;left:112px;top:840px;width:520px;font-size:14px;line-height:1.7;color:var(--muted)}
.about .btn{position:absolute;left:112px;top:1030px}
.about-photo{position:absolute;left:680px;top:720px;width:380px;height:380px;border-radius:50%;background:radial-gradient(circle at 50% 45%,#f2c7c5 0%,#b6d67a 55%,#8fb84a 100%)}
.dot{position:absolute;border-radius:50%}

/* services */
.services{position:absolute;left:0;top:1160px;width:1200px;height:800px;background:linear-gradient(180deg,#8fc23b 0%,var(--green) 50%,#9cc63a 100%);clip-path:polygon(0 40px,1200px 110px,1200px 720px,0 780px)}
.services-pattern{position:absolute;left:0;top:1160px;width:1200px;height:800px;clip-path:polygon(0 40px,1200px 110px,1200px 720px,0 780px);background:radial-gradient(circle at 10% 20%,rgba(255,255,255,.18) 0 80px,transparent 81px),radial-gradient(circle at 85% 30%,rgba(255,255,255,.15) 0 110px,transparent 111px),radial-gradient(circle at 20% 85%,rgba(60,110,20,.25) 0 120px,transparent 121px),radial-gradient(circle at 90% 80%,rgba(60,110,20,.22) 0 90px,transparent 91px)}
.services-eyebrow{position:absolute;left:0;top:1290px;width:1200px;text-align:center;color:var(--white)}
.services-head{position:absolute;left:0;top:1310px;width:1200px;text-align:center;font-family:"Montserrat",sans-serif;font-weight:500;font-size:52px;letter-spacing:2px;color:var(--white)}
.service-card{position:absolute;top:1408px;width:308px;height:372px}
.service-photo{position:absolute;left:0;top:0;width:308px;height:330px}
.service-label{position:absolute;left:20px;top:290px;width:268px;height:82px;background:var(--white);display:flex;align-items:center;justify-content:center;font-family:"Montserrat",sans-serif;font-weight:700;font-size:26px;line-height:1.15;color:var(--ink);text-align:center}
.carousel-dots{position:absolute;left:0;top:1844px;width:1200px;display:flex;justify-content:center;gap:14px}
.carousel-dots span{width:9px;height:9px;border-radius:50%;background:var(--white)}

/* quote */
.quote-band{position:absolute;left:0;top:1870px;width:1200px;height:700px;background:linear-gradient(120deg,var(--gold) 0%,var(--yellow) 45%,#f7c83a 100%);clip-path:polygon(0 70px,1200px 10px,1200px 700px,0 700px)}
.quote-photo{position:absolute;left:132px;top:2120px;width:380px;height:380px;border-radius:50%;background:radial-gradient(circle at 50% 40%,#f1ece4 0%,#cfd6da 50%,#9fb2bf 100%)}
.quote-eyebrow{position:absolute;left:420px;top:2022px;width:400px;text-align:center;color:var(--ink)}
.quote-title{position:absolute;left:320px;top:2046px;width:600px;text-align:center;font-family:"Montserrat",sans-serif;font-weight:700;font-size:46px;line-height:1.2;color:var(--ink)}
.field{position:absolute;background:var(--white);font-size:11px;color:#888;padding:8px 12px}
.quote-btn{position:absolute;left:560px;top:2384px;font-family:"Montserrat",sans-serif;font-weight:700;font-size:14px;letter-spacing:2px;color:var(--ink);background:var(--white);border-radius:30px;padding:12px 28px}

/* map & contact */
.map{position:absolute;left:0;top:2570px;width:1200px;height:470px;background:linear-gradient(135deg,#eceee9 0%,#e3e6df 50%,#dfe7d8 100%)}
.map-pin{position:absolute;left:846px;top:2770px}
.contact-card{position:absolute;left:172px;top:2584px;width:290px;height:328px;background:var(--teal);color:var(--white);padding:40px 28px;font-size:14px;font-style:normal}
.contact-row{display:flex;gap:14px;align-items:flex-start;margin-bottom:30px;line-height:1.5}
.contact-row svg{flex:none;margin-top:2px}

/* footer */
.site-footer{position:absolute;left:0;top:3040px;width:1200px;height:132px;background:var(--black);color:var(--white)}
.foot-links{position:absolute;left:112px;top:34px;display:flex;gap:32px;list-style:none;font-family:"Montserrat",sans-serif;font-size:15px;font-weight:600}
.copyright{position:absolute;left:112px;top:74px;font-size:12px;color:#bbb;letter-spacing:.5px}
.social{position:absolute;left:950px;top:42px;display:flex;gap:12px}
.social span{width:34px;height:34px;border-radius:50%;background:var(--white)}
</style>
</head>
<body>

<section class="hero">
  <div class="hero-photo" role="img" aria-label="Smiling woman in a white sports top celebrating behind a table of fresh vegetables"></div>
  <div class="hero-produce" role="img" aria-label="Fresh greens, peppers and produce along the lower edge"></div>
  <nav class="site-nav">
    <div class="brand"><span class="brand-dot"></span>Verdant Form</div>
    <span class="brand-sub">Nutritional Therapy</span>
    <ul class="nav-links">
      <li>HOME</li><li>ABOUT</li><li>COACHING</li><li>FITNESS</li><li>NUTRITION</li><li>CONTACT US</li>
    </ul>
  </nav>
  <div class="hero-copy">
    <h1 class="hero-title"><b>7 LIFESTYLE</b> <span class="amp">&amp;</span><br><span class="light">DIETARY HABITS FOR</span></h1>
    <p class="hero-script">Healthy liver &amp;<br>gallbladder functions</p>
  </div>
  <a class="btn btn-blue">BOOK NOW</a>
</section>

<section class="about">
  <span class="eyebrow">WELCOME TO</span>
  <h2>ABOUT US</h2>
  <span class="about-rule"></span>
  <p>We guide people of every age toward stronger bodies and calmer minds through practical nutrition, natural medicine and steady movement. Our team of nutritionists, naturopaths and trainers builds plans around your routine, your goals and your family life, so healthy habits feel simple to keep. Start with a friendly consultation and leave with clear next steps that fit you.</p>
  <a class="btn btn-teal">READ MORE</a>
  <div class="about-photo" role="img" aria-label="Woman in a pink top sitting cross-legged on grass in a park"></div>
  <span class="dot" style="left:980px;top:740px;width:104px;height:104px;background:var(--red)"></span>
  <span class="dot" style="left:630px;top:1018px;width:60px;height:60px;background:var(--gold)"></span>
</section>

<section class="services-section">
  <div class="services"></div>
  <div class="services-pattern" role="img" aria-label="Backdrop of fresh vegetables and herbs"></div>
  <span class="eyebrow services-eyebrow">OUR</span>
  <h2 class="services-head">SERVICES</h2>
  <article class="service-card" style="left:112px">
    <div class="service-photo" role="img" aria-label="Bowl of fresh salad with tomatoes and greens" style="background:linear-gradient(160deg,#f4efe6 0%,#c9d99a 45%,#d9533d 75%,#8fb84a 100%)"></div>
    <div class="service-label">Clinical<br>Nutritionists</div>
  </article>
  <article class="service-card" style="left:452px">
    <div class="service-photo" role="img" aria-label="Practitioner offering a natural remedy in soft light" style="background:linear-gradient(160deg,#3c6a4c 0%,#6f9a6b 50%,#2d4b3a 100%)"></div>
    <div class="service-label">Naturopaths</div>
  </article>
  <article class="service-card" style="left:780px">
    <div class="service-photo" role="img" aria-label="Group practising yoga on a beach at sunset" style="background:linear-gradient(180deg,#c9b9a8 0%,#d8c4ac 45%,#9aa6a8 70%,#c1ab8c 100%)"></div>
    <div class="service-label">Rehab Trainers</div>
  </article>
  <div class="carousel-dots"><span></span><span></span><span></span></div>
</section>

<section class="quote">
  <div class="quote-band"></div>
  <div class="quote-photo" role="img" aria-label="Woman relaxing by a bright window holding a cup"></div>
  <span class="dot" style="left:100px;top:2140px;width:104px;height:104px;background:var(--red)"></span>
  <span class="dot" style="left:488px;top:2416px;width:64px;height:64px;background:var(--teal)"></span>
  <span class="eyebrow quote-eyebrow">ONLINE BOOKING</span>
  <h2 class="quote-title">GET A QUOTE NOW</h2>
  <div class="field" style="left:560px;top:2164px;width:252px;height:30px">First name</div>
  <div class="field" style="left:828px;top:2164px;width:252px;height:30px">Last name</div>
  <div class="field" style="left:560px;top:2220px;width:520px;height:30px">Email</div>
  <div class="field" style="left:560px;top:2272px;width:520px;height:84px">Message</div>
  <a class="quote-btn">BOOK NOW</a>
</section>

<section class="map" role="img" aria-label="Street map of the neighbourhood around the studio"></section>
<svg class="map-pin" width="40" height="56" viewBox="0 0 40 56" aria-hidden="true"><path d="M20 2C10 2 3 9 3 19c0 13 17 35 17 35s17-22 17-35C37 9 30 2 20 2z" fill="#d8322e"/><circle cx="20" cy="19" r="6" fill="#8a1a18"/></svg>
<address class="contact-card">
  <div class="contact-row">
    <svg width="18" height="22" viewBox="0 0 18 22"><path d="M9 1C5 1 2 4 2 8c0 5 7 13 7 13s7-8 7-13c0-4-3-7-7-7z" fill="#fff"/><circle cx="9" cy="8" r="2.5" fill="#33b8a4"/></svg>
    <span>88 Linden Row Avenue,<br>Hollis, OR 97301</span>
  </div>
  <div class="contact-row">
    <svg width="18" height="18" viewBox="0 0 18 18"><path d="M4 1l3 4-2 2c1 2 3 4 6 6l2-2 4 3-2 3C8 17 1 10 1 3z" fill="#fff"/></svg>
    <span>1-800-555-0142</span>
  </div>
  <div class="contact-row">
    <svg width="20" height="16" viewBox="0 0 20 16"><rect x="1" y="1" width="18" height="14" rx="2" fill="#fff"/><path d="M2 3l8 6 8-6" stroke="#33b8a4" stroke-width="1.6" fill="none"/></svg>
    <span>hello@verdantform.com</span>
  </div>
</address>

<footer class="site-footer">
  <ul class="foot-links"><li>HOME</li><li>ABOUT</li><li>COACHING</li><li>FITNESS</li><li>NUTRITION</li><li>CONTACT US</li></ul>
  <p class="copyright">COPYRIGHT © 2024 | WWW.VERDANTFORM.COM</p>
  <div class="social"><span></span><span></span><span></span></div>
</footer>

</body>
</html>
```